International Business Development Firm, in need of Branded Stationery material

We just made our Logo and now we are looking for branded stationery for our company such as:

* A Letterhead with our company's name, address, and logo at the top in Word format for easy editing
* A more formal letter format with a light background design (watermark) featuring our logo, allowing us to write over it for various documents and presentations
* Business card + Envelopes are a plus but not a must
* PowerPoint for company and product introductions
* An Info sheet with Bullet Points

The design should be professional.
Please ensure the design is high quality and print ready.

Target Market(s)

Businesses and high net value individuels

Industry/Entity Type

International Business Development Firm

Colors

Designer to choose colors to be used in the design.

Requirements
Must have
• word docs so i can use the stationery templates afterwards

```html
<!DOCTYPE html>
<html lang="en">
<head>
<meta charset="utf-8">
<title>Veridel Partners – Business Card</title>
<link href="https://fonts.googleapis.com/css2?family=Open+Sans:wght@400;600;700&display=swap" rel="stylesheet">
<style>
  :root {
    --backdrop: #3a3a3a;
    --card: #151515;
    --card-edge: #222222;
    --silver: #a9a9a9;
    --purple: #6e3fa3;
    --lilac: #9d7fc4;
    --ink-light: #f2f2f2;
  }
  * { margin: 0; padding: 0; box-sizing: border-box; }
  html, body {
    width: 1200px;
    height: 689px;
    overflow: hidden;
    background: var(--backdrop);
    font-family: "Open Sans", sans-serif;
  }
  .canvas {
    position: relative;
    width: 1200px;
    height: 689px;
  }
  .card {
    position: absolute;
    top: 196px;
    width: 530px;
    height: 303px;
    background: var(--card);
    border: 1px solid var(--card-edge);
    border-radius: 18px;
  }
  .card--front { left: 50px; }
  .card--back { left: 620px; }

  .wordmark {
    display: flex;
    align-items: center;
    gap: 12px;
    font-weight: 700;
    text-transform: uppercase;
    letter-spacing: 0.06em;
    white-space: nowrap;
  }
  .wordmark__dot {
    width: 14px;
    height: 14px;
    border-radius: 50%;
    background: currentColor;
  }
  .card--front .wordmark {
    position: absolute;
    left: 0; right: 0; top: 50%;
    transform: translateY(-50%);
    justify-content: center;
    color: var(--silver);
    font-size: 38px;
  }

  .card--back .wordmark {
    position: absolute;
    left: 36px;
    top: 34px;
    color: var(--purple);
    font-size: 24px;
  }
  .card--back .wordmark__dot { width: 10px; height: 10px; }

  .person {
    position: absolute;
    left: 36px;
    top: 104px;
    padding-left: 18px;
    border-left: 10px solid var(--purple);
  }
  .person__name {
    color: var(--purple);
    font-weight: 700;
    font-size: 22px;
    line-height: 1.1;
    text-transform: uppercase;
  }
  .person__role {
    color: var(--lilac);
    font-size: 13px;
    letter-spacing: 0.03em;
    text-transform: uppercase;
    margin-top: 2px;
  }
  .address {
    position: absolute;
    left: 64px;
    top: 170px;
    color: var(--ink-light);
    font-size: 14px;
    line-height: 1.35;
  }
  .contacts {
    position: absolute;
    left: 64px;
    top: 222px;
    list-style: none;
    color: var(--ink-light);
    font-size: 14px;
    line-height: 1.45;
  }
  .contacts li {
    display: flex;
    align-items: center;
    gap: 8px;
  }
  .contacts svg { width: 13px; height: 13px; flex: none; }
</style>
</head>
<body>
<main class="canvas">
  <section class="card card--front" aria-label="Card front">
    <div class="wordmark"><span class="wordmark__dot"></span>Veridel Partners</div>
  </section>

  <section class="card card--back" aria-label="Card back">
    <div class="wordmark"><span class="wordmark__dot"></span>Veridel Partners</div>

    <div class="person">
      <p class="person__name">Daniel Moreau</p>
      <p class="person__role">Managing Director</p>
    </div>

    <p class="address">Your address, City<br>State, Zip 1234</p>

    <ul class="contacts">
      <li>
        <svg viewBox="0 0 16 16" aria-hidden="true"><path fill="var(--purple)" d="M3.6 1.2l2.3 2.6-1.3 1.8c.9 2 2.6 3.6 4.6 4.6l1.8-1.3 2.6 2.3-1.4 2.3C7.2 14.3 1.7 8.8 1.3 2.6z"/></svg>
        123 456 789
      </li>
      <li>
        <svg viewBox="0 0 16 16" aria-hidden="true"><rect x="1" y="3" width="14" height="10" rx="1.5" fill="var(--purple)"/><path d="M1.5 4l6.5 5 6.5-5" stroke="var(--card)" stroke-width="1.4" fill="none"/></svg>
        info@yourmail.com
      </li>
      <li>
        <svg viewBox="0 0 16 16" aria-hidden="true"><circle cx="8" cy="8" r="7" fill="var(--purple)"/><path d="M1 8h14M8 1c-3 3.5-3 10.5 0 14M8 1c3 3.5 3 10.5 0 14" stroke="var(--card)" stroke-width="1" fill="none"/></svg>
        www.yourwebsite.com
      </li>
    </ul>
  </section>
</main>
</body>
</html>
```